Business Card Design

We would like to re-design our business cards. Our Company - Qwinrel Turbochargers, rebuilds turbochargers and sells replacement parts. Our website is: http://www.qwinrelturbochargers-example.com
We just had our logo changed. I will attach the file. Looking for fresh new/modern business card. We like the colors red, black, white and silver. Black background looks attractive, but not a requirement. The final design should communicate reasonable/competitive prices, top quality and reliability of our products.
Updates
Project Deadline Extended
Reason: Need to finalize the info on the card. Currently working on changing address and email info. Want to make sure it is the correct one before accepting the final design. Unless, this is something that can be changed at a later time..??
Industry/Entity Type
Business
Contact Information for Business Card
QWINREL TURBOCHARGERS, LLC
20473 Harwick Lane NE
Massillon, OH 44647
Tel: +1-555-214-7390
Fax: +1-555-267-1842
info@QwinrelTurbochargers-example.com
Our current business card had the following highlights:
*We rebuild all Turbocharges for Automotive, Diesel and Industrial
*Precision Balancing and in-house turbocharger needs
*All Turbocharger replacement parts are made in USA / U.K.
Look and feel
Each slider illustrates characteristics of the customer's brand and the style your logo design should communicate.

```html
<!DOCTYPE html>
<html lang="en">
<head>
<meta charset="utf-8">
<title>Qwinrel Turbochargers — Business Card</title>
<link href="https://fonts.googleapis.com/css2?family=Open+Sans:wght@400;600;800&display=swap" rel="stylesheet">
<style>
  :root {
    --page: #2a2a2c;
    --card-white: #f4f4f4;
    --card-black: #1c1a1b;
    --brand-red: #d3222b;
    --ink: #1e1e1e;
    --ink-soft: #3a3a3a;
    --faint-red: rgba(190, 60, 55, 0.45);
    --faint-grey: #6d6b6c;
  }
  * { box-sizing: border-box; margin: 0; padding: 0; }
  html, body {
    width: 1200px; height: 800px; overflow: hidden;
    background: var(--page);
    font-family: "Open Sans", sans-serif;
  }
  .canvas {
    position: relative; width: 1200px; height: 800px;
    display: flex; align-items: center; justify-content: center; gap: 50px;
  }
  .card {
    position: relative; width: 525px; height: 300px;
    border-radius: 4px; overflow: hidden;
    box-shadow: 0 10px 30px rgba(0,0,0,0.5);
  }
  .card svg.art { position: absolute; inset: 0; }

  /* Front */
  .card-front { background: var(--card-white); color: var(--ink); }
  .brand-name {
    position: absolute; top: 34px; left: 200px;
    display: flex; align-items: center; gap: 10px;
    font-weight: 800; font-size: 26px; color: var(--ink); letter-spacing: 0.2px;
  }
  .brand-dot { width: 18px; height: 18px; border-radius: 50%; background: var(--brand-red); }
  .person {
    position: absolute; top: 94px; left: 40px;
  }
  .person-name { font-size: 19px; color: #fff; font-weight: 400; }
  .person-role { font-size: 11px; color: var(--ink-soft); margin-top: 4px; }
  .contacts {
    position: absolute; top: 158px; left: 22px;
    list-style: none; font-size: 13.5px; line-height: 19px; color: var(--ink);
  }
  .contacts li { display: flex; align-items: center; gap: 10px; }
  .contacts svg { width: 12px; height: 12px; flex: none; }
  .address-bar {
    position: absolute; left: 14px; right: 14px; bottom: 14px; height: 34px;
    background: var(--brand-red); border-radius: 17px;
    display: flex; align-items: center; padding-left: 30px;
    color: #fbe3e3; font-size: 15px;
  }

  /* Back */
  .card-back { background: linear-gradient(160deg, #2a2829, var(--card-black)); }
  .back-mark {
    position: absolute; top: 118px; left: 0; right: 0; text-align: center;
    font-weight: 800; font-size: 34px; color: var(--faint-grey);
  }
  .back-web {
    position: absolute; bottom: 64px; left: 0; right: 0; text-align: center;
    font-size: 13px; color: #d8d8d8; letter-spacing: 0.3px;
  }
</style>
</head>
<body>
<main class="canvas">

  <section class="card card-front" aria-label="Business card front">
    <svg class="art" viewBox="0 0 525 300" aria-hidden="true">
      <path class="swoosh-red" d="M0 92 C170 88 360 120 505 238 C350 150 170 128 0 132 Z" fill="var(--brand-red)"/>
      <path class="swoosh-black" d="M0 136 C170 130 350 152 505 240 C340 168 170 146 0 146 Z" fill="var(--ink)"/>
    </svg>

    <div class="brand-name"><span class="brand-dot"></span>Qwinrel Turbochargers</div>

    <div class="person">
      <p class="person-name">Marlon Tessaly</p>
      <p class="person-role">Director</p>
    </div>

    <ul class="contacts">
      <li>
        <svg viewBox="0 0 12 12"><path d="M2 1 L4.5 1 L5.5 3.5 L4 4.8 C4.8 6.5 5.5 7.2 7.2 8 L8.5 6.5 L11 7.5 L11 10 C6 10.5 1.5 6 2 1 Z" fill="var(--brand-red)"/></svg>
        +1-555-214-7390
      </li>
      <li>
        <svg viewBox="0 0 12 12"><rect x="3" y="1" width="6" height="4" fill="var(--brand-red)"/><rect x="1" y="5" width="10" height="5" rx="1" fill="var(--brand-red)"/><rect x="3" y="8" width="6" height="3" fill="#fff"/></svg>
        +1-555-267-1842
      </li>
      <li>
        <svg viewBox="0 0 12 12"><rect x="1" y="2.5" width="10" height="7" fill="var(--brand-red)"/><path d="M1 2.5 L6 6.5 L11 2.5" stroke="#fff" fill="none"/></svg>
        info@QwinrelTurbochargers-example.com
      </li>
      <li>
        <svg viewBox="0 0 12 12"><circle cx="6" cy="6" r="5" fill="var(--brand-red)"/><path d="M1 6 H11 M6 1 V11" stroke="#fff" stroke-width="0.8"/><ellipse cx="6" cy="6" rx="2.2" ry="5" stroke="#fff" stroke-width="0.8" fill="none"/></svg>
        www.qwinrelturbochargers-example.com
      </li>
    </ul>

    <div class="address-bar">4182 Brenthaven Ave. NW Dorlick. Ohio</div>
  </section>

  <section class="card card-back" aria-label="Business card back">
    <svg class="art" viewBox="0 0 525 300" aria-hidden="true">
      <path d="M40 150 C60 60 420 40 500 110 C440 70 110 70 70 150 Z" fill="var(--faint-red)"/>
      <path d="M470 170 C450 250 110 270 30 200 C100 240 420 230 450 170 Z" fill="var(--faint-red)"/>
    </svg>
    <p class="back-mark">Qwinrel Turbochargers</p>
    <p class="back-web">www.qwinrelturbochargers-example.com</p>
  </section>

</main>
</body>
</html>
```